Larkspur Talent IT Recruiting firm needs a business card design for Recruiters, Sourcers, and Account

We need business cards that allow us to change all contact info, names, titles (Recruiter, Sourcer, Account Manager, Director, CEO, etc) per person since we have three offices, in three cities, Phoenix, Austin, and Las Vegas. We do recruiting and contractors for IT positions (Developers, Architects, Software Engineers, Security Engineers, Help Desk, DBAs, PMs, Scrum Masters, etc.) Our client companies are very diverse from Meridian 100 to silicone Valley type start-ups.

So, while we what hip, techie, and quirky, it still needs to be professional. Primary color we use is blue, with silver as a secondary color.

Target Market(s)

IT, Technology

Industry/Entity Type

Business

Contact Information for Business Card

Company name: Larkspur Talent, Inc.
Website: www.larkspurtalent.example
Logos for Careerloop, Blipster, and Myriada

Name, Title, Office Number, Cell Number, email

Font styles to use
Serif
Sans Serif

Colors
0455a3
d5d5d5

Requirements
Nice to have
• The grey I selected below is not necessary - but, would like silver included. I included a card design (File 3: LTI early trial example.jpg) that I had started on. It's very rough, and not quite what we're looking for, but what we did like is the logo, big, maybe a bit faded, off center, goes out of frame, etc. Still looking for other ideas - you are the pros! But, just an idea of a design element we liked.

```html
<!DOCTYPE html>
<html lang="en">
<head>
<meta charset="utf-8">
<title>Larkspur Talent — Business Card</title>
<link rel="stylesheet" href="https://fonts.googleapis.com/css2?family=Montserrat:wght@400;500;600&display=swap">
<style>
  :root {
    --brand-blue: #0455a3;
    --brand-blue-light: #1e8ad6;
    --silver: #d5d5d5;
    --ink: #222222;
    --ink-soft: #555555;
    --paper: #ffffff;
    --backdrop: #e6e6e6;
  }
  * { margin: 0; padding: 0; box-sizing: border-box; }
  html, body {
    width: 1200px; height: 718px; overflow: hidden;
    background: radial-gradient(ellipse at center, #f4f4f4 0%, var(--backdrop) 100%);
    font-family: "Montserrat", sans-serif;
  }
  .card {
    position: absolute; left: 250px; top: 159px;
    width: 700px; height: 400px;
    background: var(--paper);
    overflow: hidden;
    box-shadow: 0 10px 30px rgba(0,0,0,0.15);
  }
  .card-shapes { position: absolute; inset: 0; }
  .brand {
    position: absolute; right: 34px; top: 58px;
    display: flex; align-items: center; gap: 12px;
  }
  .brand-dot {
    width: 34px; height: 34px; border-radius: 50%;
    background: var(--brand-blue-light);
    flex: none;
  }
  .brand-name {
    font-size: 24px; font-weight: 500; letter-spacing: 2px;
    color: var(--ink); text-transform: uppercase; white-space: nowrap;
  }
  .brand-tagline {
    position: absolute; right: 34px; top: 110px;
    font-size: 9px; letter-spacing: 2px; color: var(--ink-soft);
    text-transform: uppercase; white-space: nowrap;
  }
  .person {
    position: absolute; left: 48px; top: 150px; color: var(--paper);
  }
  .person-name { font-size: 18px; font-weight: 600; letter-spacing: 1.5px; text-transform: uppercase; }
  .person-title { font-size: 12px; font-weight: 400; margin-top: 4px; }
  .address {
    position: absolute; left: 48px; top: 215px;
    color: var(--paper); font-size: 11px; line-height: 1.5;
  }
  .contacts {
    position: absolute; left: 48px; top: 268px;
    list-style: none; color: var(--paper); font-size: 11px;
  }
  .contacts li { display: flex; align-items: center; gap: 10px; height: 21px; }
  .contacts svg { width: 11px; height: 11px; fill: var(--paper); flex: none; }
</style>
</head>
<body>
  <div class="card">
    <svg class="card-shapes" viewBox="0 0 700 400" width="700" height="400" aria-hidden="true">
      <defs>
        <linearGradient id="blueField" x1="0" y1="0" x2="1" y2="1">
          <stop offset="0" stop-color="#1e8ad6"/>
          <stop offset="1" stop-color="#0455a3"/>
        </linearGradient>
      </defs>
      <path d="M0 0 H230 C290 0 280 150 350 215 C420 280 560 300 700 330 V400 H0 Z" fill="url(#blueField)"/>
      <path d="M240 0 C300 0 290 145 362 208 C432 270 565 290 700 318" fill="none" stroke="#1a1a1a" stroke-width="4"/>
      <path d="M250 0 C310 0 300 140 374 201 C444 261 570 281 700 307" fill="none" stroke="var(--silver)" stroke-width="2"/>
    </svg>

    <div class="brand">
      <span class="brand-dot"></span>
      <span class="brand-name">Larkspur Talent</span>
    </div>
    <p class="brand-tagline">IT Recruiting &amp; Contract Staffing</p>

    <div class="person">
      <p class="person-name">Dana Whitlow</p>
      <p class="person-title">Managing Director</p>
    </div>

    <p class="address">1420 Harbor Lane,<br>Suite 8</p>

    <ul class="contacts">
      <li><svg viewBox="0 0 24 24"><path d="M6.6 10.8a15 15 0 0 0 6.6 6.6l2.2-2.2a1 1 0 0 1 1-.25 11 11 0 0 0 3.6.6 1 1 0 0 1 1 1V20a1 1 0 0 1-1 1A17 17 0 0 1 3 4a1 1 0 0 1 1-1h3.5a1 1 0 0 1 1 1 11 11 0 0 0 .6 3.6 1 1 0 0 1-.25 1z"/></svg>555 010 2233</li>
      <li><svg viewBox="0 0 24 24"><path d="M7 1h10a2 2 0 0 1 2 2v18a2 2 0 0 1-2 2H7a2 2 0 0 1-2-2V3a2 2 0 0 1 2-2zm0 3v14h10V4z"/></svg>555 010 2234</li>
      <li><svg viewBox="0 0 24 24"><path d="M2 5h20v14H2zm2 2v.5l8 5 8-5V7z"/></svg>hello@larkspurtalent.example</li>
      <li><svg viewBox="0 0 24 24"><circle cx="12" cy="12" r="10"/></svg>www.larkspurtalent.example</li>
    </ul>
  </div>
</body>
</html>
```